Business card for medical clinic

I need an upmarket, modern medical/health business card for my clinic

Contact Information for Business Card

name, address, email, qr code

```html
<!DOCTYPE html>
<html lang="en">
<head>
<meta charset="utf-8">
<title>Business Card</title>
<link href="https://fonts.googleapis.com/css2?family=Montserrat:wght@400;500;700&display=swap" rel="stylesheet">
<style>
  :root {
    --page: #ecebe8;
    --card-top: #efeae3;
    --card-bottom: #e2d9cf;
    --teal: #1d6f86;
    --teal-bright: #2b8fa6;
    --ink: #3a3836;
    --band: #1f1e1d;
    --band-text: #cdbfae;
  }
  html, body {
    margin: 0;
    width: 1200px;
    height: 1047px;
    overflow: hidden;
    background: var(--page);
    font-family: "Montserrat", sans-serif;
  }
  .card {
    position: absolute;
    left: 100px;
    top: 251px;
    width: 878px;
    height: 478px;
    transform: scale(1.1389);
    transform-origin: top left;
    border-radius: 20px;
    overflow: hidden;
    background: linear-gradient(160deg, var(--card-top), var(--card-bottom));
    box-shadow: 0 10px 30px rgba(0,0,0,0.12);
  }
  .brand {
    position: absolute;
    left: 36px;
    top: 78px;
    display: flex;
    align-items: center;
    gap: 16px;
  }
  .brand-dot {
    width: 26px;
    height: 26px;
    border-radius: 50%;
    background: var(--teal);
  }
  .brand-name {
    font-weight: 500;
    font-size: 30px;
    letter-spacing: 2px;
    color: var(--teal);
    line-height: 1.15;
  }
  .person {
    position: absolute;
    right: 44px;
    top: 44px;
    text-align: right;
  }
  .person-name {
    font-weight: 700;
    font-size: 29px;
    letter-spacing: 0.5px;
    color: var(--teal);
    margin: 0;
  }
  .person-role {
    font-size: 21px;
    color: var(--ink);
    margin: 2px 0 0;
  }
  .accent-bar {
    position: absolute;
    right: 0;
    top: 48px;
    width: 22px;
    height: 58px;
    background: linear-gradient(180deg, var(--teal), var(--teal-bright));
  }
  .address {
    position: absolute;
    left: 35px;
    top: 262px;
    font-size: 22px;
    line-height: 34px;
    color: var(--ink);
  }
  .contact-band {
    position: absolute;
    left: 0;
    top: 352px;
    width: 770px;
    height: 126px;
    background: linear-gradient(90deg, #2a2928, var(--band) 60%, #151414);
    border-top-right-radius: 4px;
  }
  .contact-list {
    list-style: none;
    margin: 0;
    padding: 8px 0 0 35px;
  }
  .contact-list li {
    display: flex;
    align-items: center;
    gap: 10px;
    font-size: 22px;
    line-height: 34px;
    color: var(--band-text);
  }
  .contact-list svg {
    width: 18px;
    height: 18px;
    fill: var(--band-text);
  }
  .corner-ring {
    position: absolute;
    left: 740px;
    top: 350px;
    width: 124px;
    height: 124px;
    border-radius: 50%;
    border: 6px solid var(--teal);
    box-sizing: border-box;
    background: var(--card-bottom);
  }
</style>
</head>
<body>
  <div class="card">
    <div class="brand">
      <span class="brand-dot"></span>
      <span class="brand-name">MERIDIA CARE<br>PARTNERS</span>
    </div>

    <div class="person">
      <p class="person-name">DANIEL HART</p>
      <p class="person-role">Managing Director</p>
    </div>
    <div class="accent-bar"></div>

    <div class="address">Your address, City<br>State, Zip 1234</div>

    <div class="contact-band">
      <ul class="contact-list">
        <li>
          <svg viewBox="0 0 24 24" aria-hidden="true"><path d="M3 9c0-2 4-4 9-4s9 2 9 4v2h-5V9H8v2H3z M6 12h12l2 8H4z"/></svg>
          123 456 789
        </li>
        <li>
          <svg viewBox="0 0 24 24" aria-hidden="true"><path d="M2 6h20v12H2z M4 8l8 5 8-5v-1H4z" fill-rule="evenodd"/></svg>
          info@yourgmail.com
        </li>
        <li>
          <svg viewBox="0 0 24 24" aria-hidden="true"><circle cx="12" cy="12" r="10"/></svg>
          www.yourwebsite.com
        </li>
      </ul>
    </div>
    <div class="corner-ring"></div>
  </div>
</body>
</html>
```